New Web Site Design - Tallow Ridge Communication Solutions

We are looking for a completely new web site design. Tallow Ridge Communication Solutions is a full service company providing PBX and IP/Cloud Based phone systems. We also sell and install video camera surveillance systems and provide low voltage cabling services (CAT5 and CAT3). We are looking for something professional looking. We want to be able to showcase our vendor partners as well as be able to show photos of some of the work we have done. We will also want to be able to post PDF brochures as well as make changes to the website ourselves.

Target Market(s)

Commercial

Industry/Entity Type

Communication

Coding

Coded - Design and coding required

Number of Pages Required

5+ page

Font styles to use
Sans Serif

Colors
0455a3

Requirements
Must have
• Ability to upload PDF brochures
• Professional look and feel
• Ability to upload and easily insert job photos
• Thinking it should have at least 6 pages: Main page, phone systems and services page, carrier services page, video surveillance systems and service page, low voltage cabling services page, contact us page

```html
<!DOCTYPE html>
<html lang="en">
<head>
<meta charset="utf-8">
<title>Tallow Ridge Communication Solutions</title>
<link href="https://fonts.googleapis.com/css2?family=Open+Sans:wght@300;400;600&family=Open+Sans+Condensed:wght@300&display=swap" rel="stylesheet">
<style>
:root{
  --brand:#0455a3;
  --brand-mid:#2c6fc2;
  --brand-light:#4a90d9;
  --band:#1f4f94;
  --footer:#0d3a7a;
  --footer-text:#4f74a8;
  --ink:#333a44;
  --muted:#b3b8bf;
  --grey-bg:#f1f1f1;
  --white:#ffffff;
}
*{margin:0;padding:0;box-sizing:border-box}
html,body{width:1200px;height:4138px;overflow:hidden}
body{font-family:"Open Sans",Arial,sans-serif;font-weight:300;color:var(--ink);background:var(--white);position:relative}
.btn-doc{position:absolute;width:58px;height:54px;background:var(--brand-mid);display:flex;align-items:center;justify-content:center}
/* hero */
.hero{position:absolute;left:0;top:0;width:1200px;height:772px;background:radial-gradient(ellipse at 55% 35%,#6aa3d8 0%,#3f78b4 40%,#1f4675 100%)}
.hero .photo{position:absolute;inset:0}
.logo{position:absolute;left:97px;top:50px;color:var(--white);font-size:16px;font-weight:400;line-height:1.2}
.nav{position:absolute;top:82px;left:688px;display:flex;gap:32px;font-size:13px;font-weight:400;color:var(--white)}
.hero h1{position:absolute;top:300px;left:0;width:1200px;text-align:center;font-family:"Open Sans Condensed","Arial Narrow",sans-serif;font-weight:300;font-size:104px;line-height:1.1;color:var(--white)}
.arrow{position:absolute;top:410px}
/* services band */
.services{position:absolute;top:772px;left:0;width:1200px;height:469px;background:var(--band)}
.service{position:absolute;top:60px;width:320px}
.service h2{margin-top:40px;font-weight:300;font-size:52px;line-height:1;color:var(--white)}
.service h2 span{display:block;color:var(--brand-light)}
.service p{margin-top:14px;font-size:14px;line-height:1.3;color:#7a9fd0;font-weight:400}
/* intro */
.intro{position:absolute;top:1241px;left:97px;width:1006px}
.intro h2{font-weight:300;font-size:52px;line-height:1.02;color:var(--ink)}
.intro h2 span{display:block;color:var(--brand-mid)}
.intro .lead{margin-top:30px;font-size:15px;font-weight:400}
.intro .body{margin-top:18px;font-size:12px;line-height:1.6;color:var(--muted);font-weight:400}
.more{position:absolute;top:378px;left:0;display:flex;height:61px}
.more .label{width:124px;background:#3a3f46;color:var(--white);font-size:13px;font-weight:400;display:flex;align-items:center;justify-content:center}
.more .icon{width:58px;background:var(--brand-mid);display:flex;align-items:center;justify-content:center}
/* features */
.features-bg{position:absolute;top:2014px;left:0;width:1200px;height:491px;background:var(--grey-bg)}
.card{position:absolute;top:1801px;width:318px;height:585px;background:var(--white)}
.card .img{height:213px}
.card h3{margin:50px 0 0 50px;font-weight:300;font-size:38px;line-height:1;color:var(--brand-mid)}
.card p{margin:22px 50px 0 50px;font-size:12px;line-height:1.6;color:var(--muted);font-weight:400}
.card .btn-doc{left:0;bottom:0;width:58px;height:55px}
/* deals */
.deals{position:absolute;top:2505px;left:0;width:1200px;height:436px;background:linear-gradient(100deg,#4e5258 0%,#7b7f86 45%,#9a9ea4 70%,#6f737a 100%)}
.deals h2{position:absolute;left:97px;top:148px;font-weight:300;font-size:52px;line-height:1.05;color:var(--white)}
.deals p{position:absolute;left:97px;top:264px;font-size:15px;color:#d8dade;font-weight:400}
.deals .go{position:absolute;left:974px;top:160px;width:127px;height:121px;background:var(--brand-mid);display:flex;align-items:center;justify-content:center}
/* plans */
.plan{position:absolute;top:3040px;width:240px}
.plan .speed{font-size:88px;font-weight:300;line-height:1;color:var(--ink)}
.plan .speed small{font-size:36px;margin-left:6px}
.plan h3{margin-top:24px;font-weight:300;font-size:36px;line-height:1;color:var(--brand-mid)}
.plan .perks{margin-top:12px;font-size:16px;line-height:1.3;font-weight:400;color:var(--ink)}
.plan p.small{margin-top:14px;font-size:12px;line-height:1.55;color:var(--muted);font-weight:400;width:220px}
.plan .btn-doc{top:350px;left:0;width:60px;height:59px}
/* footer */
.footer{position:absolute;top:3567px;left:0;width:1200px;height:571px;background:var(--footer)}
.fcol{position:absolute;top:92px;width:240px}
.fcol h4{font-weight:400;font-size:16px;color:var(--footer-text);margin-bottom:24px}
.fcol li{list-style:none;font-size:12px;font-weight:400;color:var(--footer-text);height:34px;padding-left:22px;position:relative}
.fcol li::before{content:"";position:absolute;left:2px;top:5px;width:5px;height:5px;border-right:2px solid var(--footer-text);border-top:2px solid var(--footer-text);transform:rotate(45deg)}
.copy{position:absolute;right:102px;top:450px;font-size:11px;color:var(--footer-text);font-weight:400}
.social{position:absolute;top:485px;width:64px;height:64px;border-radius:50%;background:#1a4d94}
.social.first{background:var(--brand-light)}
</style>
</head>
<body>

<header class="hero">
  <div class="photo" role="img" aria-label="Open hand in a suit sleeve holding a smartphone in front of a glowing dotted world map"></div>
  <div class="logo">Tallow Ridge<br>Communication Solutions</div>
  <nav class="nav"><span>HOME</span><span>ABOUT</span><span>SERVICES</span><span>BLOG</span><span>CONTACTS</span></nav>
  <h1>SPEED &amp; QUALITY</h1>
  <svg class="arrow" style="left:84px" width="30" height="46" viewBox="0 0 30 46"><path d="M24 4 L7 23 L24 42" fill="none" stroke="#fff" stroke-width="6"/></svg>
  <svg class="arrow" style="left:1080px" width="30" height="46" viewBox="0 0 30 46"><path d="M6 4 L23 23 L6 42" fill="none" stroke="#fff" stroke-width="6"/></svg>
</header>

<section class="services">
  <div class="service" style="left:97px">
    <svg width="68" height="60" viewBox="0 0 68 60"><rect x="2" y="14" width="64" height="44" rx="4" fill="#fff"/><rect x="22" y="4" width="24" height="12" rx="3" fill="none" stroke="#fff" stroke-width="5"/><rect x="2" y="32" width="64" height="4" fill="#1f4f94"/><rect x="29" y="29" width="10" height="10" fill="#fff"/></svg>
    <h2>BUSINESS<span>SOLUTIONS</span></h2>
    <p>QUISQUE GRAVIDA FELIS EU MASSA<br>CONSECTETUR AT MALES PORTTITOR.</p>
  </div>
  <div class="service" style="left:441px">
    <svg width="64" height="60" viewBox="0 0 64 60"><path d="M32 4 L2 32 L10 32 L10 58 L26 58 L26 40 L38 40 L38 58 L54 58 L54 32 L62 32 Z" fill="#fff"/></svg>
    <h2>HOME<span>SOLUTIONS</span></h2>
    <p>QUISQUE GRAVIDA FELIS EU MASSA<br>CONSECTETUR AT MALES PORTTITOR.</p>
  </div>
  <div class="service" style="left:783px">
    <svg width="60" height="60" viewBox="0 0 60 60"><circle cx="30" cy="30" r="28" fill="#fff"/><path d="M14 16 C22 14 26 20 22 26 C18 30 24 36 20 44 C14 38 10 28 14 16 Z M34 10 C42 12 48 18 50 26 C44 26 40 30 42 38 C36 40 34 32 30 28 C34 22 30 16 34 10 Z" fill="#1f4f94"/></svg>
    <h2>UNLIMITED<span>INTERNET</span></h2>
    <p>QUISQUE GRAVIDA FELIS EU MASSA<br>CONSECTETUR AT MALES PORTTITOR.</p>
  </div>
  <div class="btn-doc" style="left:99px;top:373px;background:#3f74b8"><svg width="20" height="24" viewBox="0 0 20 24"><path d="M2 2 H13 L18 7 V22 H2 Z" fill="none" stroke="#fff" stroke-width="2"/><path d="M6 11 H14 M6 15 H14" stroke="#fff" stroke-width="2"/></svg></div>
  <div class="btn-doc" style="left:441px;top:373px;background:#3f74b8"><svg width="20" height="24" viewBox="0 0 20 24"><path d="M2 2 H13 L18 7 V22 H2 Z" fill="none" stroke="#fff" stroke-width="2"/><path d="M6 11 H14 M6 15 H14" stroke="#fff" stroke-width="2"/></svg></div>
  <div class="btn-doc" style="left:785px;top:373px;background:#3f74b8"><svg width="20" height="24" viewBox="0 0 20 24"><path d="M2 2 H13 L18 7 V22 H2 Z" fill="none" stroke="#fff" stroke-width="2"/><path d="M6 11 H14 M6 15 H14" stroke="#fff" stroke-width="2"/></svg></div>
</section>

<section class="intro" style="padding-top:70px">
  <h2>FAST DOWNLOAD AND UPLOAD SPEEDS<span>AT AN AFFORDABLE PRICE</span></h2>
  <p class="lead">QUISQUE GRAVIDA FELIS EU MASSA CONSECTETUR AT MALES PORTTITOR.</p>
  <p class="body">Our fiber-backed network keeps every office line, camera feed and cloud call moving without pause. We plan, install and support phone systems, surveillance and structured cabling for businesses of every size, with clear pricing and local technicians ready when you need them. Each project starts with a site survey and ends with a tested, documented installation your team can trust.</p>
  <div class="more"><span class="label">MORE INFO</span><span class="icon"><svg width="20" height="24" viewBox="0 0 20 24"><path d="M2 2 H13 L18 7 V22 H2 Z" fill="none" stroke="#fff" stroke-width="2"/><path d="M6 11 H14 M6 15 H14" stroke="#fff" stroke-width="2"/></svg></span></div>
</section>

<div class="features-bg"></div>
<article class="card" style="left:99px">
  <div class="img" role="img" aria-label="Office desk with a keyboard, papers and colleagues working" style="background:linear-gradient(135deg,#e9edf2,#c9d3de 60%,#9aa6b4)"></div>
  <h3>EQUIPMENT<br>INSTALLATION<br>AND SETUP</h3>
  <p>Certified technicians mount, wire and test every handset, camera and switch so your system works on day one.</p>
  <div class="btn-doc"><svg width="20" height="24" viewBox="0 0 20 24"><path d="M2 2 H13 L18 7 V22 H2 Z" fill="none" stroke="#fff" stroke-width="2"/><path d="M6 11 H14 M6 15 H14" stroke="#fff" stroke-width="2"/></svg></div>
</article>
<article class="card" style="left:441px">
  <div class="img" role="img" aria-label="Support agent wearing a headset" style="background:linear-gradient(90deg,#cfe0ef,#f2f4f6 55%,#d9dde2)"></div>
  <h3>CUSTOMER<br>SUPPORT<br>CENTER</h3>
  <p>Reach a real person by phone or ticket around the clock for answers, repairs and account changes fast.</p>
  <div class="btn-doc"><svg width="20" height="24" viewBox="0 0 20 24"><path d="M2 2 H13 L18 7 V22 H2 Z" fill="none" stroke="#fff" stroke-width="2"/><path d="M6 11 H14 M6 15 H14" stroke="#fff" stroke-width="2"/></svg></div>
</article>
<article class="card" style="left:783px">
  <div class="img" role="img" aria-label="Business people in a meeting looking at a tablet" style="background:linear-gradient(135deg,#dfe4ea,#b3c0cf 55%,#7f8fa3)"></div>
  <h3>CUSTOMER<br>SATISFACTION<br>GUARANTEE</h3>
  <p>If a service falls short we make it right, with clear terms and no hidden fees on your bill.</p>
  <div class="btn-doc"><svg width="20" height="24" viewBox="0 0 20 24"><path d="M2 2 H13 L18 7 V22 H2 Z" fill="none" stroke="#fff" stroke-width="2"/><path d="M6 11 H14 M6 15 H14" stroke="#fff" stroke-width="2"/></svg></div>
</article>

<section class="deals" role="img" aria-label="Hands typing on a white keyboard, darkened background">
  <h2>FIND THE BEST DEALS<br>IN YOUR AREA</h2>
  <p>QUISQUE GRAVIDA FELIS EU MASSA CONSECTETUR AT MALES PORTTITOR.</p>
  <div class="go"><svg width="26" height="24" viewBox="0 0 26 24"><path d="M2 12 H14 M9 6 L15 12 L9 18" fill="none" stroke="#fff" stroke-width="3"/><path d="M14 2 H24 V22 H14" fill="none" stroke="#fff" stroke-width="3"/></svg></div>
</section>

<div class="plan" style="left:97px">
  <div class="speed">10<small>MBPS</small></div><h3>STARTER</h3>
  <div class="perks">ACCESS TO 100,000<br>WIFI HOTSPOTS AT<br>NO EXTRA COST</div>
  <p class="small">Clear voice and steady data for small offices with light daily traffic and few users.</p>
  <div class="btn-doc"><svg width="20" height="24" viewBox="0 0 20 24"><path d="M2 2 H13 L18 7 V22 H2 Z" fill="none" stroke="#fff" stroke-width="2"/><path d="M6 11 H14 M6 15 H14" stroke="#fff" stroke-width="2"/></svg></div>
</div>
<div class="plan" style="left:353px">
  <div class="speed">20<small>MBPS</small></div><h3>HOME</h3>
  <div class="perks">ACCESS TO 100,000<br>WIFI HOTSPOTS AT<br>NO EXTRA COST</div>
  <p class="small">Room for more calls, cloud backups and a handful of cameras on one reliable line.</p>
  <div class="btn-doc"><svg width="20" height="24" viewBox="0 0 20 24"><path d="M2 2 H13 L18 7 V22 H2 Z" fill="none" stroke="#fff" stroke-width="2"/><path d="M6 11 H14 M6 15 H14" stroke="#fff" stroke-width="2"/></svg></div>
</div>
<div class="plan" style="left:610px">
  <div class="speed">30<small>MBPS</small></div><h3>EXTREME</h3>
  <div class="perks">ACCESS TO 100,000<br>WIFI HOTSPOTS AT<br>NO EXTRA COST</div>
  <p class="small">Built for busy teams running video meetings, surveillance feeds and heavy file transfers.</p>
  <div class="btn-doc"><svg width="20" height="24" viewBox="0 0 20 24"><path d="M2 2 H13 L18 7 V22 H2 Z" fill="none" stroke="#fff" stroke-width="2"/><path d="M6 11 H14 M6 15 H14" stroke="#fff" stroke-width="2"/></svg></div>
</div>
<div class="plan" style="left:869px">
  <div class="speed">40<small>MBPS</small></div><h3>PERFORMANCE</h3>
  <div class="perks">ACCESS TO 100,000<br>WIFI HOTSPOTS AT<br>NO EXTRA COST</div>
  <p class="small">Top tier capacity for multi-site firms that need constant uptime and priority service.</p>
  <div class="btn-doc"><svg width="20" height="24" viewBox="0 0 20 24"><path d="M2 2 H13 L18 7 V22 H2 Z" fill="none" stroke="#fff" stroke-width="2"/><path d="M6 11 H14 M6 15 H14" stroke="#fff" stroke-width="2"/></svg></div>
</div>

<footer class="footer">
  <div class="fcol" style="left:97px"><h4>SUPPORT</h4><ul><li>ONLINE SUPPORT</li><li>PROGRAM POLICY</li><li>IDENTITY GUIDELINES</li><li>DEVELOPMENT PROCESS</li></ul></div>
  <div class="fcol" style="left:353px"><h4>MEMBERSHIP</h4><ul><li>CONTACT US</li><li>HELP</li><li>SUPPORT SYSTEM</li><li>REFUNDS</li><li>SITE MAP</li></ul></div>
  <div class="fcol" style="left:610px"><h4>DEVELOPERS</h4><ul><li>MOBILE DEVELOPERS</li><li>DESKTOP DEVELOPERS</li><li>RELEASE CHANNELS</li><li>IDENTITY GUIDELINES</li><li>BETA SUPPORT</li></ul></div>
  <div class="fcol" style="left:869px"><h4>LICENSE</h4><ul><li>ONLINE VERIFICATION</li><li>RENEWAL LICENSE</li><li>REPORT ILLEGAL</li><li>MORE INFORMATION</li><li>FAQS</li></ul></div>
  <div class="copy">© 2015 | Privacy Policy</div>
  <div class="social first" style="left:873px" aria-label="News feed"></div>
  <div class="social" style="left:953px" aria-label="Social profile"></div>
  <div class="social" style="left:1036px" aria-label="Social profile"></div>
</footer>

</body>
</html>
```